business card

Business card for new business.
Red and black corporate colors.
Card can have an Indsutrial feel to it. Feel free to add Rust, Bolted steel, or graphics as you see fit. We provide highly specialized services to the below mentioned industries.
Keep information out of corners so that if I want I can choose rounded corners.
Information
- front. name - title - phone - email
- Rear
Pipelines - Ports - Heavy Civil Works - Quarrying - Power
Ironvale - Stonebridge - Red Pine Crossing - Castleford - Westhaven

```html
<!DOCTYPE html>
<html lang="en">
<head>
<meta charset="utf-8">
<title>Girderline Business Card</title>
<link rel="stylesheet" href="https://fonts.googleapis.com/css2?family=Lato:wght@400;700;900&display=swap">
<style>
  :root {
    --backdrop: #353535;
    --card: #000000;
    --red: #e21f26;
    --steel: #7e7e7e;
    --white: #ffffff;
  }
  html, body {
    margin: 0;
    padding: 0;
    width: 1200px;
    height: 1200px;
    overflow: hidden;
    background: var(--backdrop);
    font-family: "Lato", sans-serif;
  }
  .sheet {
    width: 1200px;
    height: 1200px;
    display: flex;
    flex-direction: column;
    align-items: center;
    justify-content: center;
    gap: 60px;
  }
  .card {
    position: relative;
    width: 820px;
    height: 469px;
    background: var(--card);
    overflow: hidden;
  }
  .brand {
    display: flex;
    align-items: center;
    gap: 18px;
  }
  .brand-mark {
    width: 24px;
    height: 24px;
    background: var(--red);
  }
  .brand-name {
    font-weight: 900;
    font-size: 78px;
    line-height: 1;
    letter-spacing: 1px;
    color: var(--steel);
  }

  /* Rear side */
  .card-rear .brand {
    position: absolute;
    top: 140px;
    left: 0;
    right: 0;
    justify-content: center;
  }
  .card-rear .service-lines {
    position: absolute;
    top: 290px;
    left: 0;
    right: 0;
    text-align: center;
    color: var(--white);
    font-size: 22px;
    line-height: 1.45;
    letter-spacing: 0.3px;
  }
  .sep {
    display: inline-block;
    width: 6px;
    height: 6px;
    border-radius: 50%;
    background: var(--red);
    margin: 0 9px;
    vertical-align: middle;
  }

  /* Front side */
  .card-front .brand {
    position: absolute;
    top: 78px;
    left: 80px;
  }
  .person {
    position: absolute;
    left: 70px;
    bottom: 92px;
  }
  .person-name {
    margin: 0;
    color: var(--red);
    font-weight: 700;
    font-size: 34px;
    letter-spacing: 0.5px;
    text-transform: uppercase;
  }
  .person-title {
    margin: 4px 0 0;
    color: var(--white);
    font-size: 24px;
  }
  .contact {
    position: absolute;
    left: 530px;
    top: 210px;
    color: var(--white);
    font-size: 21px;
    line-height: 1.35;
  }
  .address {
    margin: 0 0 18px;
    font-style: normal;
  }
  .contact-list {
    list-style: none;
    margin: 0;
    padding: 0;
  }
  .contact-list li {
    display: flex;
    align-items: center;
    gap: 14px;
  }
  .contact-list svg {
    width: 18px;
    height: 18px;
    flex: none;
  }
  .accent-band {
    position: absolute;
    left: 0;
    right: 0;
    bottom: 0;
    height: 11px;
    background: var(--red);
  }
</style>
</head>
<body>
<main class="sheet">

  <section class="card card-rear" aria-label="Card rear">
    <div class="brand">
      <span class="brand-mark"></span>
      <span class="brand-name">GIRDERLINE</span>
    </div>
    <div class="service-lines">
      <div class="industries">Pipelines<span class="sep"></span>Ports<span class="sep"></span>Heavy Civil Works<span class="sep"></span>Quarrying<span class="sep"></span>Power</div>
      <div class="cities">Ironvale<span class="sep"></span>Stonebridge<span class="sep"></span>Red Pine Crossing<span class="sep"></span>Castleford<span class="sep"></span>Westhaven</div>
    </div>
  </section>

  <section class="card card-front" aria-label="Card front">
    <div class="brand">
      <span class="brand-mark"></span>
      <span class="brand-name">GIRDERLINE</span>
    </div>

    <div class="person">
      <h1 class="person-name">Daniel Okafor</h1>
      <p class="person-title">Manager</p>
    </div>

    <div class="contact">
      <address class="address">418 Foundry Road<br>Houston, TX 77021</address>
      <ul class="contact-list">
        <li>
          <svg viewBox="0 0 24 24" aria-hidden="true"><path fill="#e21f26" d="M6.6 10.8a15.1 15.1 0 0 0 6.6 6.6l2.2-2.2a1 1 0 0 1 1-.25 11.4 11.4 0 0 0 3.6.57 1 1 0 0 1 1 1V20a1 1 0 0 1-1 1A17 17 0 0 1 3 4a1 1 0 0 1 1-1h3.5a1 1 0 0 1 1 1c0 1.25.2 2.45.57 3.57a1 1 0 0 1-.25 1z"/></svg>
          <span>512 555 0142</span>
        </li>
        <li>
          <svg viewBox="0 0 24 24" aria-hidden="true"><rect x="2" y="5" width="20" height="14" fill="#e21f26"/><path d="M2 5l10 8 10-8" fill="none" stroke="#000" stroke-width="1.8"/></svg>
          <span>info@girderline.com</span>
        </li>
        <li>
          <svg viewBox="0 0 24 24" aria-hidden="true"><g fill="none" stroke="#e21f26" stroke-width="2"><circle cx="12" cy="12" r="9.5"/><ellipse cx="12" cy="12" rx="4" ry="9.5"/><path d="M2.5 12h19M4 7h16M4 17h16"/></g></svg>
          <span>www.girderline.com</span>
        </li>
      </ul>
    </div>

    <div class="accent-band"></div>
  </section>

</main>
</body>
</html>
```